Ward Compass Business Card Design*

We need a business card design for our company Ward Compass. Our company is specialized in providing online consulting services regarding medical institutions, hospitals and doctors. We work with patients worldwide looking to choose between healthcare providers. We have a website you may use as a reference, where we list doctors and clinics worldwide. So we target Medical providers as well as patients worldwide.
Target Market(s)
Medical Providers and patients around the world
Industry/Entity Type
Medical
Contact Information for Business Card
Salwa Kettani
CEO
+90 612 348 2175
info@wardcompass.example
www.wardcompass.example
14 Annakhil 7 H.R.B. Rabat, Morocco
Requirements
Must have
- Company logo/name on one full side, personal info and smaller logo and company name on the other side.
Nice to have
- Smart and elegant design

```html
<!DOCTYPE html>
<html lang="en">
<head>
<meta charset="utf-8">
<title>Ward Compass Business Card</title>
<link href="https://fonts.googleapis.com/css2?family=Poppins:wght@300;400;500;600&display=swap" rel="stylesheet">
<style>
  :root {
    --navy: #163d6e;
    --navy-deep: #123563;
    --band-light: #4e7196;
    --band-dark: #1f4a7a;
    --steel: #9a9ea3;
    --paper: #ffffff;
    --ink: #2b2f36;
    --backdrop: #e9e7e3;
  }
  * { box-sizing: border-box; margin: 0; padding: 0; }
  html, body {
    width: 1200px; height: 910px; overflow: hidden;
    background: var(--backdrop);
    font-family: "Poppins", sans-serif;
  }
  .canvas { position: relative; width: 1200px; height: 910px; }

  .card {
    position: absolute;
    box-shadow: 0 14px 30px rgba(0,0,0,.18), 0 2px 5px rgba(0,0,0,.12);
    overflow: hidden;
  }

  /* Front side */
  .card--front {
    left: 60px; top: 272px; width: 640px; height: 366px;
    background: var(--paper);
  }
  .front-swoosh { position: absolute; inset: 0; width: 100%; height: 100%; }
  .holder {
    position: absolute; right: 34px; top: 24px; text-align: right; color: var(--paper);
  }
  .holder__name { font-size: 26px; font-weight: 500; letter-spacing: .2px; line-height: 1.1; }
  .holder__role { font-size: 12px; font-weight: 400; letter-spacing: 1px; margin-top: 2px; }

  .brand {
    position: absolute; left: 40px; top: 226px;
    display: flex; align-items: center; gap: 12px;
  }
  .brand__dot { width: 34px; height: 34px; border-radius: 50%; background: var(--navy); }
  .brand__name {
    font-size: 25px; font-weight: 600; color: var(--navy); letter-spacing: .5px;
  }

  .contacts {
    position: absolute; left: 126px; top: 280px; list-style: none;
    font-size: 13px; color: var(--ink); line-height: 21px;
  }
  .contacts li { display: flex; align-items: center; gap: 9px; }
  .contacts svg { width: 11px; height: 11px; flex: none; }

  .address {
    position: absolute; right: 34px; top: 206px; text-align: right;
    font-size: 13px; font-style: normal; color: var(--ink); line-height: 19px;
  }

  /* Back side */
  .card--back {
    left: 770px; top: 135px; width: 366px; height: 640px;
    background: var(--navy-deep);
  }
  .back-url {
    position: absolute; left: 40px; top: 40px;
    transform-origin: left top; transform: rotate(90deg) translateY(-14px);
    color: var(--paper); font-size: 13px; letter-spacing: 3.2px; white-space: nowrap;
  }
  .back-brand {
    position: absolute; left: 0; right: 0; top: 270px;
    display: flex; flex-direction: column; align-items: center; gap: 14px;
  }
  .back-brand__dot { width: 40px; height: 40px; border-radius: 50%; background: var(--paper); }
  .back-brand__name {
    color: var(--paper); font-size: 30px; font-weight: 600; letter-spacing: 1px; text-align: center; line-height: 1.15;
  }
</style>
</head>
<body>
<main class="canvas">

  <section class="card card--front" aria-label="Business card front">
    <svg class="front-swoosh" viewBox="0 0 640 366" preserveAspectRatio="none" aria-hidden="true">
      <defs>
        <linearGradient id="bandFill" x1="0" y1="0" x2="1" y2="1">
          <stop offset="0" stop-color="#1f4a7a"/>
          <stop offset=".55" stop-color="#1f4a7a"/>
          <stop offset="1" stop-color="#4e7196"/>
        </linearGradient>
      </defs>
      <path class="band-edge" d="M640,112 C430,100 170,122 0,196" fill="none" stroke="#9a9ea3" stroke-width="6"/>
      <path class="band" d="M0,0 H640 V106 C430,94 170,116 0,190 Z" fill="url(#bandFill)"/>
    </svg>

    <div class="holder">
      <p class="holder__name">Salwa Kettani</p>
      <p class="holder__role">CEO</p>
    </div>

    <div class="brand">
      <span class="brand__dot"></span>
      <span class="brand__name">WARD COMPASS</span>
    </div>

    <ul class="contacts">
      <li>
        <svg viewBox="0 0 12 12" aria-hidden="true"><path d="M2.5 1 L4.5 1 L5 3.5 L3.8 4.5 C4.4 6 5.9 7.5 7.5 8.2 L8.5 7 L11 7.5 L11 9.5 C11 10.3 10.3 11 9.5 11 C5 11 1 7 1 2.5 C1 1.7 1.7 1 2.5 1 Z" fill="#163d6e"/></svg>
        +90 612 348 2175
      </li>
      <li>
        <svg viewBox="0 0 12 12" aria-hidden="true"><rect x="0.5" y="2" width="11" height="8" rx="1" fill="#163d6e"/><path d="M1 2.8 L6 6.6 L11 2.8" fill="none" stroke="#fff" stroke-width="1"/></svg>
        info@wardcompass.example
      </li>
      <li>
        <svg viewBox="0 0 12 12" aria-hidden="true"><circle cx="6" cy="6" r="5.5" fill="#163d6e"/><path d="M0.8 6 H11.2 M6 0.6 C3.5 3 3.5 9 6 11.4 M6 0.6 C8.5 3 8.5 9 6 11.4" fill="none" stroke="#fff" stroke-width=".8"/></svg>
        www.wardcompass.example
      </li>
    </ul>

    <address class="address">
      14 Annakhil 7<br>H.R.B. Rabat, Morocco
    </address>
  </section>

  <section class="card card--back" aria-label="Business card back">
    <p class="back-url">www.wardcompass.example</p>
    <div class="back-brand">
      <span class="back-brand__dot"></span>
      <p class="back-brand__name">WARD<br>COMPASS</p>
    </div>
  </section>

</main>
</body>
</html>
```